Truck Outfitters and Trailer Hitch Retailer Website

We are working with a hitch installer in California called Brisk Tow. They sell and install trailer hitches, bedliners for trucks, and pickup truck accessories.
Some sites to use for content/competitors:
https://www.varlomi.com/pick-up-outfitters
https://bramwells-rigs.com
https://www.thetowlodge.com
https://towlodgeinccom.quenrivsites.com
Some sites to use for inspiration:
https://www.ironmarkcouplers.com
https://quietcouplers.com
https://velmatow.com/
https://www.harborcoat.com
https://www.rugged-trailpath.com
Thank you for taking the time to consider designing a website for us. We are web developers based in Stockton, CA, USA. Most of our projects go through the same process. Understanding this process may help you win a project with us. We custom-code all of our websites in-house. We don’t have any requirements as to what tools you use for your design, but we prefer Figma files. For any design that we label as four-stars, we send it to the client for review. The client picks the final design they want us to use. Once we complete this process, we will continue to show additional clients all the four-star sites and purchase them later. Your designs will have multiple chances to sell. For better chances of success, we ask that you follow these guidelines.
IMAGES:
If you use any images or icons in the design, we ask that you have a link to the asset so we can purchase the image/icon. Most of the designs we submit do not have the customer’s images on them unless they have some great images. Be creative; show us the feeling you are trying to portray with your image choices. Use any royalty-free site you choose. We subscribe to Adobe and mainly use their images, but we can purchase images outside of Adobe.
PLEASE NOTE: we will not submit designs to clients with watermarks on the images.
FONTS:
We ask that you identify the fonts used in the design. This can be done in a message if you want. We typically use Google Fonts and Adobe Fonts.
CONTENT:
We're always open to different content and ideas. We often submit designs with stock images so the client can see our vision. We typically take pictures after the website launch to use their images with our vision. Lorem Ipsum is fine for paragraphs, but we ask that you write the headers in correct English. We want to be able to show the vision and identify the sections of the website.
INSPIRATION:
We typically add a couple of links in the brief of websites we like to help you get started in your design.
REVISIONS:
We do not often ask for revisions of the designs unless we see something in the design that may not appeal to the client. If there are slight changes that we want to make, we do that in the development process.
FEEDBACK:
We rarely give feedback on designs during the design process. We are working on many website projects and do not have the time to provide feedback. We usually respond if your request is well thought out and asks specific questions, but a note asking “feedback, please” usually goes unanswered
Number of Pages Required
1 page
Look and feel
Each slider illustrates characteristics of the customer's brand and the style your logo design should communicate.

```html
<!DOCTYPE html>
<html lang="en">
<head>
<meta charset="UTF-8">
<title>Brisk Tow — Trailer Hitches &amp; Truck Accessories</title>
<link href="https://fonts.googleapis.com/css2?family=Orbitron:wght@700;900&family=Poppins:wght@400;500;600&display=swap" rel="stylesheet">
<style>
:root{
  --red:#e10a0a;
  --black:#000;
  --ink:#111;
  --grey-band:#3f3f3f;
  --footer:#262626;
  --white:#fff;
  --muted:#bdbdbd;
  --gold:#f2b617;
}
*{box-sizing:border-box;margin:0;padding:0}
html,body{width:1200px;height:4181px;overflow:hidden;background:var(--black)}
body{font-family:'Poppins',sans-serif;color:var(--white);position:relative}
.display{font-family:'Orbitron',sans-serif;font-weight:900;text-transform:uppercase;letter-spacing:1px}
section,header,nav,footer{position:absolute;left:0;width:1200px}
.abs{position:absolute}
.btn{position:absolute;background:var(--red);color:var(--white);border-radius:6px;font-family:'Orbitron',sans-serif;font-weight:900;font-size:13px;text-transform:uppercase;display:flex;align-items:center;justify-content:center;letter-spacing:.5px}

/* header */
.site-header{top:0;height:119px;background:var(--black)}
.search{left:84px;top:44px;width:379px;height:47px;border:1px solid #555;border-radius:24px;display:flex;align-items:center;padding-left:8px;font-size:12px;color:#ddd}
.search .dot{width:33px;height:33px;border-radius:50%;background:var(--red);display:flex;align-items:center;justify-content:center;margin-right:12px}
.brand{left:485px;top:28px;width:200px;text-align:center}
.brand-name{font-family:'Orbitron',sans-serif;font-weight:900;font-size:22px;color:var(--white);text-transform:uppercase;letter-spacing:1px}
.brand-tag{font-size:10px;color:var(--muted);font-weight:600;margin-top:2px}
.round{position:absolute;width:38px;height:38px;border-radius:50%;background:var(--red);display:flex;align-items:center;justify-content:center}
.phone-label{left:758px;top:46px;font-family:'Orbitron',sans-serif;font-weight:900;font-size:10px;text-transform:uppercase}
.phone-num{left:758px;top:66px;font-size:14px}

.main-nav{top:119px;height:47px;background:var(--red);display:flex;justify-content:center;align-items:center;gap:34px;font-size:13.5px}

/* hero */
.hero{top:166px;height:600px;background:linear-gradient(180deg,#6d8fb4 0%,#9fb4c8 35%,#6f7c6a 52%,#5d6166 70%,#4a4d52 100%)}
.hero-title{left:100px;top:205px;font-size:38px}
.hero-sub{left:100px;top:260px;font-size:28px}

/* services */
.services{top:766px;height:752px;background:var(--black)}
.section-title{position:absolute;left:0;width:1200px;text-align:center;font-size:27px}
.card{position:absolute;top:184px;width:320px;height:471px;background:var(--white);border-radius:9px;overflow:hidden;color:var(--ink)}
.card .photo{height:208px}
.card h3{position:absolute;left:24px;top:240px;color:var(--red);font-size:17px}
.card p{position:absolute;left:30px;top:276px;width:270px;font-size:13.5px;line-height:26.5px}
.card .btn{left:30px;top:395px;width:143px;height:38px}

/* about */
.about{top:1518px;height:536px;background:var(--grey-band)}
.about h2{left:659px;top:120px;font-size:27px}
.about p{position:absolute;left:656px;width:460px;font-size:14px;line-height:29.5px}

/* features */
.features{top:2054px;height:743px;background:var(--black)}
.features .sub{position:absolute;left:0;width:1200px;text-align:center;top:176px;font-size:16px}
.feat{position:absolute;width:330px}
.feat h4{font-family:'Orbitron',sans-serif;font-weight:900;font-size:14px;text-transform:uppercase;line-height:22px;letter-spacing:.5px}
.feat p{font-size:13px;line-height:24px;margin-top:4px}
.feat.left{text-align:right}

/* testimonials */
.testimonials{top:2797px;height:544px;background:var(--red)}
.quote{position:absolute;left:160px;width:880px;top:308px;text-align:center;font-size:16px;line-height:28.5px}
.stars{position:absolute;left:0;width:1200px;text-align:center;top:404px;color:var(--gold);font-size:16px;letter-spacing:1px}
.reviewer{position:absolute;left:0;width:1200px;text-align:center;top:437px;font-size:17px}

/* contact */
.contact{top:3341px;height:467px;background:var(--black)}
.contact h2{left:103px;top:97px;font-size:27px}
.info{position:absolute;left:102px;display:flex;align-items:flex-start;gap:18px;font-size:14px;line-height:23px}
.info .round{position:static;width:40px;height:40px;flex:none}
.info strong{font-weight:500;font-size:17px}
.field{position:absolute;background:var(--white);border-radius:5px;color:#555;font-size:14px;padding:10px 13px}

/* footer */
.site-footer{top:3808px;height:373px;background:var(--footer)}
.foot-brand{position:absolute;left:0;width:1200px;top:90px;text-align:center}
.foot-brand .brand-name{font-size:34px}
.foot-brand .brand-tag{font-size:15px;color:var(--white);letter-spacing:1px}
.foot-nav{position:absolute;top:237px;left:0;width:1200px;display:flex;justify-content:center;gap:34px;font-size:13.5px}
.rule{position:absolute;left:104px;top:294px;width:992px;height:1px;background:#777}
.copy{position:absolute;left:0;width:1200px;top:318px;text-align:center;font-size:13px}
</style>
</head>
<body>

<header class="site-header">
  <div class="abs search">
    <span class="dot"><svg width="16" height="16" viewBox="0 0 16 16"><circle cx="7" cy="7" r="4.5" fill="none" stroke="#fff" stroke-width="2"/><line x1="10.5" y1="10.5" x2="14" y2="14" stroke="#fff" stroke-width="2.2" stroke-linecap="round"/></svg></span>
    Search Product......
  </div>
  <div class="abs brand">
    <div class="brand-name">Brisk Tow</div>
    <div class="brand-tag">Built to haul every load</div>
  </div>
  <span class="round" style="left:709px;top:48px"><svg width="18" height="18" viewBox="0 0 24 24"><path fill="#fff" d="M6.6 10.8a15.1 15.1 0 0 0 6.6 6.6l2.2-2.2c.3-.3.7-.4 1-.2 1.1.4 2.3.6 3.6.6.6 0 1 .4 1 1V20c0 .6-.4 1-1 1A17 17 0 0 1 3 4c0-.6.4-1 1-1h3.5c.6 0 1 .4 1 1 0 1.3.2 2.5.6 3.6.1.3 0 .7-.2 1z"/></svg></span>
  <div class="abs phone-label">Phone Number :</div>
  <div class="abs phone-num">+1 555 014 2273</div>
  <span class="round" style="left:1006px;top:48px"><svg width="18" height="18" viewBox="0 0 24 24"><path fill="#fff" d="M12 21s-8-5.2-8-11a4.5 4.5 0 0 1 8-2.8A4.5 4.5 0 0 1 20 10c0 5.8-8 11-8 11z"/></svg></span>
  <span class="round" style="left:1058px;top:48px"><svg width="18" height="18" viewBox="0 0 24 24"><path fill="#fff" d="M3 4h3l2.4 10h10l2-7H7.5l-.5-2H3z"/><circle cx="9.5" cy="18" r="1.7" fill="#fff"/><circle cx="17" cy="18" r="1.7" fill="#fff"/></svg></span>
</header>

<nav class="main-nav">
  <span>Home</span><span>PRODUCTS</span><span>What Size Hitch Do I need?</span><span>COMPANY</span><span>Dealer Locator</span><span>Become A Dealer</span><span>Contact us</span>
</nav>

<section class="hero" role="img" aria-label="Silver wagon towing a car on a flatbed trailer along a mountain highway">
  <h1 class="abs display hero-title">Brisk Tow</h1>
  <div class="abs hero-sub">Built to haul every load</div>
  <div class="btn" style="left:100px;top:318px;width:142px;height:41px">Shop Now</div>
</section>

<section class="services">
  <h2 class="section-title display" style="top:124px">Services and Products</h2>
  <article class="card" style="left:101px">
    <div class="photo" role="img" aria-label="Car carrier truck loaded with vehicles" style="background:linear-gradient(160deg,#c9cdd2,#8ea6c2 45%,#6b5a4c)"></div>
    <h3 class="display">Truck Outfitters</h3>
    <p>Lorem ipsum dolor sit amet, consectetur adipiscing elit, sed do eiusmod tempor incididunt ut labore et dolore magna aliqua.</p>
    <div class="btn">Shop Now</div>
  </article>
  <article class="card" style="left:438px">
    <div class="photo" role="img" aria-label="Mesh-sided utility trailer" style="background:linear-gradient(180deg,#d9d9d9,#9a9a96 60%,#6d6d6a)"></div>
    <h3 class="display">Hitch Retailer</h3>
    <p>Lorem ipsum dolor sit amet, consectetur adipiscing elit, sed do eiusmod tempor incididunt ut labore et dolore magna aliqua.</p>
    <div class="btn">Shop Now</div>
  </article>
  <article class="card" style="left:776px">
    <div class="photo" role="img" aria-label="Small box trailer parked on grass" style="background:linear-gradient(180deg,#8d8a7e,#b8b9b4 45%,#5f8a3c)"></div>
    <h3 class="display">Truck Accessories</h3>
    <p>Lorem ipsum dolor sit amet, consectetur adipiscing elit, sed do eiusmod tempor incididunt ut labore et dolore magna aliqua.</p>
    <div class="btn">Shop Now</div>
  </article>
</section>

<section class="about">
  <svg class="abs" style="left:0;top:0" width="640" height="536" viewBox="0 0 640 536">
    <defs>
      <linearGradient id="aboutPhoto" x1="0" y1="0" x2="0" y2="1">
        <stop offset="0" stop-color="#6c8196"/>
        <stop offset=".38" stop-color="#aab3b8"/>
        <stop offset=".5" stop-color="#a88a6c"/>
        <stop offset=".72" stop-color="#6a655f"/>
        <stop offset="1" stop-color="#3b3d40"/>
      </linearGradient>
    </defs>
    <path d="M0 0H374A270 270 0 0 1 392 536H0Z" fill="var(--red)"/>
    <path role="img" aria-label="Pickup truck towing an off-road buggy on a trailer across the desert" d="M0 0H374A270 270 0 0 1 374 536H0Z" fill="url(#aboutPhoto)"/>
  </svg>
  <h2 class="abs display">About Us</h2>
  <p style="top:168px">Lorem ipsum dolor sit amet, consectetur adipiscing elit, sed do eiusmod tempor incididunt ut labore et dolore magna aliqua. Quis ipsum suspendisse ultrices gravida.</p>
  <p style="top:264px">Sed ut perspiciatis unde omnis iste natus error sit voluptatem accusantium doloremque laudantium, totam rem aperiam, eaque ipsa quae ab illo inventore veritatis et quasi architecto beatae vitae dicta sunt explicabo.</p>
  <div class="btn" style="left:656px;top:395px;width:144px;height:37px">Read More</div>
</section>

<section class="features">
  <h2 class="section-title display" style="top:136px">Features &amp; Benefits</h2>
  <div class="sub">trucks, vans, jeeps, trailers, off-road vehicles, accessories, and more...</div>

  <svg class="abs" style="left:391px;top:247px" width="420" height="420" viewBox="0 0 420 420">
    <circle cx="210" cy="210" r="205" fill="none" stroke="var(--red)" stroke-width="2" stroke-dasharray="6 5"/>
    <circle role="img" aria-label="White flatbed truck parked under trees" cx="210" cy="210" r="190" fill="#6f8a5a"/>
  </svg>

  <span class="round" style="left:427px;top:265px;width:72px;height:72px"><svg width="34" height="34" viewBox="0 0 24 24" fill="none" stroke="#fff" stroke-width="1.6"><path d="M12 3l7 3v5c0 5-3 8-7 10-4-2-7-5-7-10V6z"/><path d="M8.5 12l2.5 2.5 4.5-5"/></svg></span>
  <span class="round" style="left:698px;top:265px;width:72px;height:72px"><svg width="34" height="34" viewBox="0 0 24 24" fill="none" stroke="#fff" stroke-width="1.6"><path d="M6 4c-1 2 1 3 0 5M10 4c-1 2 1 3 0 5M14 4c-1 2 1 3 0 5"/><path d="M3 17h18M5 20h14"/></svg></span>
  <span class="round" style="left:417px;top:554px;width:72px;height:72px"><svg width="34" height="34" viewBox="0 0 24 24" fill="none" stroke="#fff" stroke-width="1.6"><path d="M12 3l8 4.5v9L12 21l-8-4.5v-9z"/><circle cx="12" cy="12" r="3.5"/></svg></span>
  <span class="round" style="left:706px;top:554px;width:72px;height:72px"><svg width="34" height="34" viewBox="0 0 24 24" fill="none" stroke="#fff" stroke-width="1.6"><path d="M12 3c3 4 5 6.5 5 9a5 5 0 0 1-10 0c0-2.5 2-5 5-9z"/><path d="M4 20h16"/></svg></span>

  <div class="feat left" style="left:65px;top:267px">
    <h4>Lifetime Warranty</h4>
    <p>Lorem ipsum dolor sit amet, consectetur adipiscing elit,&nbsp; et dolore magna aliqua.</p>
  </div>
  <div class="feat" style="left:818px;top:275px">
    <h4>Dries to the touch in<br>under 10 seconds</h4>
    <p>Lorem ipsum dolor sit amet, consectetur adipiscing elit,&nbsp; et dolore magna aliqua.</p>
  </div>
  <div class="feat left" style="left:65px;top:568px">
    <h4>Prevents rust leaks and<br>corrosion</h4>
    <p>Lorem ipsum dolor sit amet, consectetur adipiscing elit,&nbsp; et dolore magna aliqua.</p>
  </div>
  <div class="feat" style="left:810px;top:568px;width:360px">
    <h4>Scratch and dent resistant</h4>
    <p>Lorem ipsum dolor sit amet, consectetur adipiscing elit,&nbsp; et dolore magna aliqua.</p>
  </div>
</section>

<section class="testimonials">
  <h2 class="section-title display" style="top:134px">Testimonials</h2>
  <svg class="abs" style="left:554px;top:193px" width="94" height="94" viewBox="0 0 94 94"><circle role="img" aria-label="Customer portrait" cx="47" cy="47" r="47" fill="#7c8a93"/></svg>
  <p class="quote">Lorem ipsum dolor sit amet, consectetur adipiscing elit, sed do eiusmod tempor incididunt ut labore et dolore magna aliqua. Quis ipsum suspendisse ultrices gravida. Risus commodo viverra maecenas accumsan lacus vel facilisis.</p>
  <div class="stars">★★★★★</div>
  <div class="reviewer display">- Dale Morrow</div>
</section>

<section class="contact">
  <h2 class="abs display">Contact Us</h2>
  <div class="info" style="top:166px">
    <span class="round"><svg width="16" height="18" viewBox="0 0 24 24"><path fill="#fff" d="M12 2a7 7 0 0 0-7 7c0 5 7 13 7 13s7-8 7-13a7 7 0 0 0-7-7zm0 9.5A2.5 2.5 0 1 1 12 6.5a2.5 2.5 0 0 1 0 5z"/></svg></span>
    <div>253,Brisk Tow Lorem ipsum dolor<br>sit amet, adipiscing</div>
  </div>
  <div class="info" style="top:240px">
    <span class="round"><svg width="17" height="17" viewBox="0 0 24 24"><path fill="#fff" d="M6.6 10.8a15.1 15.1 0 0 0 6.6 6.6l2.2-2.2c.3-.3.7-.4 1-.2 1.1.4 2.3.6 3.6.6.6 0 1 .4 1 1V20c0 .6-.4 1-1 1A17 17 0 0 1 3 4c0-.6.4-1 1-1h3.5c.6 0 1 .4 1 1 0 1.3.2 2.5.6 3.6.1.3 0 .7-.2 1z"/></svg></span>
    <div><strong>Phone Number :</strong><br>+1 555 014 2273</div>
  </div>
  <div class="info" style="top:311px">
    <span class="round"><svg width="18" height="16" viewBox="0 0 24 20"><rect x="2" y="2" width="20" height="16" rx="2" fill="#fff"/><path d="M2 4l10 7 10-7" fill="none" stroke="var(--red)" stroke-width="2"/></svg></span>
    <div><strong>Email Us :</strong><br>info@brisktow.in</div>
  </div>

  <div class="field" style="left:533px;top:79px;width:271px;height:43px">First Name</div>
  <div class="field" style="left:822px;top:79px;width:271px;height:43px">Last Name</div>
  <div class="field" style="left:533px;top:142px;width:271px;height:43px">Email</div>
  <div class="field" style="left:822px;top:142px;width:271px;height:43px">Phone Number</div>
  <div class="field" style="left:533px;top:206px;width:562px;height:125px">Message</div>
  <div class="btn" style="left:531px;top:347px;width:143px;height:41px">Submit</div>
</section>

<footer class="site-footer">
  <div class="foot-brand">
    <div class="brand-name">Brisk Tow</div>
    <div class="brand-tag">Built to haul every load</div>
  </div>
  <nav class="foot-nav">
    <span>Home</span><span>PRODUCTS</span><span>What Size Hitch Do I need?</span><span>COMPANY</span><span>Dealer Locator</span><span>Become A Dealer</span><span>Contact us</span>
  </nav>
  <div class="rule"></div>
  <div class="copy">© 2024 Brisk Tow | All rights reserved</div>
</footer>

</body>
</html>
```